Brightfen Business Card Redesign & Logo Update

We need to update our business cards to something more modern and fresh. Brightfen can provide the current color schemes and old design examples, but welcome creativity in helping us with this redesign. PLEASE NOTE that we no longer utilize the "tree" and/or "leaf" imagery in our branding. If able would apprecaite an update on the quality of our "words only" logo in Ai. / PNG formats too.

Target Market(s)

Investors, landowners, corporate partners, contractors

Industry/Entity Type

Environmental Restoration & Conservation

Contact Information for Business Card

Logo, persons name, title, mailing address, phone and email, website url

Font styles to use
Other font styles liked:
• Merriweather

Requirements
Nice to have
• Logo, persons name, title, mailing address, phone and email, website url, but open to ideams
Should not have
• No all back backgrounds

```html
<!DOCTYPE html>
<html lang="en">
<head>
<meta charset="UTF-8">
<title>Brightfen Business Card</title>
<link rel="stylesheet" href="https://fonts.googleapis.com/css2?family=Bebas+Neue&family=Poppins:wght@400&display=swap">
<style>
  :root {
    --page-bg: #e9e7e6;
    --card-light: #f3eeee;
    --brand-green: #137d3a;
    --brand-orange: #f07f0a;
    --ink-light: #ffffff;
  }
  html, body {
    margin: 0;
    padding: 0;
    width: 1200px;
    height: 900px;
    overflow: hidden;
    background: var(--page-bg);
  }
  .canvas {
    position: relative;
    width: 1200px;
    height: 900px;
  }
  .business-card {
    position: absolute;
    left: 100px;
    top: 141px;
    width: 1000px;
    height: 618px;
    background: var(--card-light);
    overflow: hidden;
    box-shadow: 0 10px 30px rgba(0,0,0,0.15);
  }
  .card-shapes {
    position: absolute;
    inset: 0;
    width: 100%;
    height: 100%;
  }
  .shape-accent { fill: var(--brand-orange); }
  .shape-panel { fill: var(--brand-green); }

  .brand-block {
    position: absolute;
    left: 50px;
    top: 138px;
    width: 390px;
    text-align: center;
  }
  .brand-name {
    font-family: "Bebas Neue", sans-serif;
    font-weight: 400;
    font-size: 108px;
    line-height: 0.9;
    color: var(--brand-green);
    letter-spacing: 1px;
    margin: 0;
  }

  .contact-panel {
    position: absolute;
    left: 545px;
    top: 104px;
    color: var(--ink-light);
    font-family: "Poppins", sans-serif;
  }
  .person-name {
    font-family: "Bebas Neue", sans-serif;
    font-size: 56px;
    line-height: 0.9;
    margin: 0;
    font-weight: 400;
  }
  .person-title {
    font-size: 28px;
    line-height: 1.1;
    margin: 0;
  }
  .mailing-address {
    font-style: normal;
    font-size: 28px;
    line-height: 36px;
    margin-top: 40px;
  }
  .contact-list {
    list-style: none;
    margin: 46px 0 0;
    padding: 0;
    font-size: 28px;
    line-height: 37px;
  }
  .contact-list li {
    display: flex;
    align-items: center;
    gap: 8px;
  }
  .contact-icon {
    width: 28px;
    height: 28px;
    flex: none;
    fill: none;
    stroke: var(--ink-light);
    stroke-width: 2;
  }
</style>
</head>
<body>
<div class="canvas">
  <div class="business-card">
    <svg class="card-shapes" viewBox="0 0 1000 618" preserveAspectRatio="none" aria-hidden="true">
      <path class="shape-accent" d="M440 0 C500 60 510 120 480 260 C455 380 420 470 460 618 L1000 618 L1000 0 Z"/>
      <path class="shape-panel" d="M480 0 C535 70 530 150 500 270 C470 380 440 480 460 618 L1000 618 L1000 0 Z"/>
    </svg>

    <div class="brand-block">
      <h1 class="brand-name">Brightfen</h1>
    </div>

    <div class="contact-panel">
      <h2 class="person-name">Marcus Hale</h2>
      <p class="person-title">Managing Director</p>
      <address class="mailing-address">421, Address line<br>goes here<br>45452,Country Name</address>
      <ul class="contact-list">
        <li>
          <svg class="contact-icon" viewBox="0 0 24 24" aria-hidden="true"><path d="M5 3h4l2 5-2.5 1.5a11 11 0 0 0 6 6L16 13l5 2v4a2 2 0 0 1-2 2A17 17 0 0 1 3 5a2 2 0 0 1 2-2z"/></svg>
          <span>021-555 014 362</span>
        </li>
        <li>
          <svg class="contact-icon" viewBox="0 0 24 24" aria-hidden="true"><rect x="3" y="6" width="18" height="12"/><path d="M3 6l9 7 9-7"/></svg>
          <span>hello@brightfen.co</span>
        </li>
        <li>
          <svg class="contact-icon" viewBox="0 0 24 24" aria-hidden="true"><circle cx="12" cy="12" r="9"/><path d="M3 12h18M12 3c3 3 3 15 0 18M12 3c-3 3-3 15 0 18"/></svg>
          <span>www.brightfen.co</span>
        </li>
      </ul>
    </div>
  </div>
</div>
</body>
</html>
```